Firm Stationery Design

I need a design for stationery, including: Stationery First Page, Stationery Second Sheet, Envelope, Mailing Label for Flat Envelopes, and Business Cards

```html
<!DOCTYPE html>
<html lang="en">
<head>
<meta charset="utf-8">
<title>Harrow Law LLC — Stationery</title>
<link href="https://fonts.googleapis.com/css2?family=Montserrat:wght@400;500;700;800&display=swap" rel="stylesheet">
<style>
  :root{
    --bg:#a3a3a3;
    --bg-light:#b5b4b5;
    --paper:#ffffff;
    --ink:#1d1d1b;
    --orange:#f7a21b;
    --orange-deep:#b8721e;
    --orange-soft:#fbbd5a;
    --muted:#5a5a5a;
    --rule:#444;
  }
  *{box-sizing:border-box;margin:0;padding:0}
  html,body{width:1200px;height:957px;overflow:hidden;background:var(--bg);font-family:"Montserrat",sans-serif;color:var(--ink)}
  .canvas{position:relative;width:1200px;height:957px;background:var(--bg)}
  .folder-zone{position:absolute;left:650px;top:0;width:550px;height:523px;background:var(--bg-light)}
  .item{position:absolute;background:var(--paper);box-shadow:2px 3px 6px rgba(0,0,0,.35)}
  .pattern{background:linear-gradient(100deg,var(--orange-soft) 0%,var(--orange) 45%,var(--orange-deep) 100%)}

  /* wordmark */
  .wordmark{display:flex;align-items:center;gap:4px;font-weight:800;color:var(--ink);white-space:nowrap;text-transform:uppercase;letter-spacing:.02em}
  .wordmark .dot{display:inline-block;background:var(--orange)}

  .address{color:var(--ink);line-height:1.35;border-left:1px solid var(--orange)}
  .contact li{list-style:none;display:flex;align-items:center;gap:3px;line-height:1.45}
  .contact .ico{display:inline-block;width:4px;height:4px;border-radius:1px;background:var(--orange)}

  /* business card back */
  .card-dark{background:var(--ink);color:#fff}
  .card-dark .wordmark{color:#fff}
  .card-name{position:absolute;right:6px;top:10px;text-align:right}
  .card-name strong{display:block;color:var(--orange);font-size:7.5px;font-weight:700;letter-spacing:.02em}
  .card-name span{font-size:4.8px}
  .card-corner{position:absolute;right:0;bottom:0;width:64px;height:60px;background:var(--orange)}
  .card-corner i{position:absolute;left:0;top:0;width:28px;height:60px;background:#fff}

  /* letter */
  .letter-body{font-size:2.6px;line-height:1.55;color:var(--muted)}
  .letter-body p{margin-bottom:4px}

  /* envelope */
  .flap{position:absolute;left:0;top:0;width:100%;height:33px;background:var(--orange);border-radius:0 0 14px 14px}

  /* notebook */
  .ruled{position:absolute;left:7px;right:7px;border-top:1px solid var(--rule)}
  .spine{position:absolute;left:136px;top:0;width:8px;height:100%;background:repeating-linear-gradient(180deg,#222 0 2px,transparent 2px 6px)}
  .spiral{position:absolute;left:-6px;top:0;width:8px;height:100%;background:repeating-linear-gradient(180deg,#111 0 2px,transparent 2px 11px)}
  .date{position:absolute;right:8px;top:14px;font-size:4.4px;color:var(--ink)}

  .compliments{position:absolute;right:12px;bottom:10px;font-size:10px;color:var(--ink)}
  .compliments span{color:var(--orange)}

  .pocket-dark{position:absolute;left:0;bottom:0;width:100%;height:50px;background:var(--ink)}
  .pocket-orange{position:absolute;left:0;bottom:0;width:100%;height:50px;background:var(--orange)}
  .bar{height:2px;background:#ccc;margin-bottom:3px}
</style>
</head>
<body>
<main class="canvas">
  <div class="folder-zone"></div>

  <!-- Business card front -->
  <div class="item pattern" style="left:78px;top:77px;width:165px;height:95px" role="img" aria-label="Repeating orange chevron pattern"></div>

  <!-- Business card back -->
  <div class="item card-dark" style="left:78px;top:185px;width:165px;height:94px">
    <div class="wordmark" style="position:absolute;left:7px;top:28px;font-size:7px"><i class="dot" style="width:6px;height:6px"></i>Harrow Law LLC</div>
    <div class="card-name"><strong>DANIEL REYES</strong><span>Managing Director</span></div>
    <div style="position:absolute;left:7px;top:53px;font-size:4.8px;line-height:1.35">Your address, City<br>State, Zip 1234</div>
    <ul class="contact" style="position:absolute;left:7px;top:70px;font-size:4.8px">
      <li><i class="ico"></i>123 456 789</li>
      <li><i class="ico"></i>info@harrowlawllc.com</li>
      <li><i class="ico"></i>www.harrowlawllc.com</li>
    </ul>
    <div class="card-corner"><i></i></div>
  </div>

  <!-- Letterhead first page -->
  <div class="item" style="left:257px;top:78px;width:141px;height:200px">
    <div class="wordmark" style="position:absolute;left:12px;top:24px;font-size:4.6px"><i class="dot" style="width:4px;height:4px"></i>Harrow Law LLC</div>
    <div class="address" style="position:absolute;left:92px;top:10px;padding-left:3px;font-size:2.8px">
      Your address, City<br>State, Zip 1234
      <ul class="contact" style="margin-top:2px"><li><i class="ico" style="width:2px;height:2px"></i>123 456 789</li><li><i class="ico" style="width:2px;height:2px"></i>info@harrowlawllc.com</li><li><i class="ico" style="width:2px;height:2px"></i>www.harrowlawllc.com</li></ul>
    </div>
    <div style="position:absolute;left:13px;top:53px;font-size:2.8px;line-height:1.5">MARISA COLE<br><span style="color:var(--muted)">Chief Executive Officer<br>City State, Zip Code</span></div>
    <div class="letter-body" style="position:absolute;left:13px;top:76px;width:116px">
      <p>Thank you for choosing our firm. We have reviewed your file and prepared a summary of the next steps, filing dates and documents we still need from you before the hearing.</p>
      <p>Please sign the enclosed forms and return them in the prepaid envelope. Our office will confirm receipt by phone within two working days.</p>
      <p>Should you have any questions, do not hesitate to contact me directly.</p>
    </div>
    <div style="position:absolute;left:13px;top:155px;font-size:2.6px;color:var(--muted)">Sincerely,</div>
    <div style="position:absolute;left:13px;top:165px;width:18px;border-top:1px solid var(--ink)"></div>
    <div style="position:absolute;left:13px;top:167px;font-size:2.8px">Owen Clarke</div>
  </div>

  <!-- Envelope front -->
  <div class="item" style="left:412px;top:79px;width:209px;height:90px">
    <div class="wordmark" style="position:absolute;left:8px;top:24px;font-size:5px"><i class="dot" style="width:4px;height:4px"></i>Harrow Law LLC</div>
    <div class="address" style="position:absolute;left:36px;top:9px;padding-left:4px;font-size:3.4px">Your address, City<br>State, Zip 1234</div>
  </div>

  <!-- Envelope back -->
  <div class="item" style="left:409px;top:185px;width:210px;height:92px">
    <div class="flap"></div>
  </div>

  <!-- Notebook cover -->
  <div class="item pattern" style="left:78px;top:309px;width:140px;height:199px" role="img" aria-label="Notebook cover with repeating orange chevron pattern">
    <div class="spiral"></div>
  </div>

  <!-- Notebook open -->
  <div class="item" style="left:302px;top:311px;width:280px;height:197px;background:#f4f4f4">
    <div class="wordmark" style="position:absolute;left:7px;top:18px;font-size:4.6px"><i class="dot" style="width:4px;height:4px"></i>Harrow Law LLC</div>
    <div class="date" style="right:150px">Date......./....../......</div>
    <div class="wordmark" style="position:absolute;left:148px;top:18px;font-size:4.6px"><i class="dot" style="width:4px;height:4px"></i>Harrow Law LLC</div>
    <div class="date">Date......./....../......</div>
    <div class="spine"></div>
    <div style="position:absolute;left:0;top:0;width:136px;height:100%">
      <div class="ruled" style="top:34px"></div><div class="ruled" style="top:42px"></div><div class="ruled" style="top:50px"></div><div class="ruled" style="top:58px"></div><div class="ruled" style="top:66px"></div><div class="ruled" style="top:74px"></div><div class="ruled" style="top:82px"></div><div class="ruled" style="top:90px"></div><div class="ruled" style="top:98px"></div><div class="ruled" style="top:106px"></div><div class="ruled" style="top:114px"></div><div class="ruled" style="top:122px"></div><div class="ruled" style="top:130px"></div><div class="ruled" style="top:138px"></div><div class="ruled" style="top:146px"></div><div class="ruled" style="top:154px"></div><div class="ruled" style="top:162px"></div><div class="ruled" style="top:170px"></div><div class="ruled" style="top:178px"></div><div class="ruled" style="top:186px"></div>
    </div>
    <div style="position:absolute;left:144px;top:0;width:136px;height:100%">
      <div class="ruled" style="top:34px"></div><div class="ruled" style="top:42px"></div><div class="ruled" style="top:50px"></div><div class="ruled" style="top:58px"></div><div class="ruled" style="top:66px"></div><div class="ruled" style="top:74px"></div><div class="ruled" style="top:82px"></div><div class="ruled" style="top:90px"></div><div class="ruled" style="top:98px"></div><div class="ruled" style="top:106px"></div><div class="ruled" style="top:114px"></div><div class="ruled" style="top:122px"></div><div class="ruled" style="top:130px"></div><div class="ruled" style="top:138px"></div><div class="ruled" style="top:146px"></div><div class="ruled" style="top:154px"></div><div class="ruled" style="top:162px"></div><div class="ruled" style="top:170px"></div><div class="ruled" style="top:178px"></div><div class="ruled" style="top:186px"></div>
    </div>
  </div>

  <!-- Folder outside, flat -->
  <div class="item" style="left:760px;top:80px;width:170px;height:230px">
    <div class="wordmark" style="position:absolute;left:14px;top:90px;font-size:13px"><i class="dot" style="width:10px;height:10px"></i>Harrow Law LLC</div>
    <div style="position:absolute;right:10px;top:170px;font-size:5px;text-align:right;line-height:1.35">Your address, City<br>State, Zip 1234</div>
    <ul class="contact" style="position:absolute;left:12px;bottom:12px;font-size:5px">
      <li><i class="ico"></i>123 456 789</li><li><i class="ico"></i>info@harrowlawllc.com</li><li><i class="ico"></i>www.harrowlawllc.com</li>
    </ul>
  </div>
  <div class="item pattern" style="left:930px;top:80px;width:170px;height:230px" role="img" aria-label="Folder back with repeating orange chevron pattern"></div>

  <!-- Folder inside, flat -->
  <div class="item" style="left:760px;top:330px;width:170px;height:160px;background:#ececec">
    <div class="pocket-dark"></div>
  </div>
  <div class="item" style="left:930px;top:330px;width:170px;height:160px;background:#f2f2f2">
    <div style="position:absolute;left:20px;top:8px;width:120px;height:120px;background:#fff;box-shadow:0 1px 3px rgba(0,0,0,.25);padding:8px">
      <div class="wordmark" style="font-size:4.2px;margin-bottom:12px"><i class="dot" style="width:3px;height:3px"></i>Harrow Law LLC</div>
      <div class="bar" style="width:40%"></div><div class="bar"></div><div class="bar"></div><div class="bar" style="width:80%"></div><div class="bar"></div><div class="bar"></div>
    </div>
    <div class="pocket-orange"></div>
  </div>

  <!-- Letterhead first page, flat large -->
  <div class="item" style="left:78px;top:586px;width:356px;height:267px">
    <div class="wordmark" style="position:absolute;left:25px;top:54px;font-size:12px"><i class="dot" style="width:9px;height:9px"></i>Harrow Law LLC</div>
    <div class="address" style="position:absolute;left:90px;top:24px;padding-left:8px;font-size:9px;height:34px;display:flex;align-items:center">Your address, City<br>State, Zip 1234</div>
  </div>

  <!-- Second sheet -->
  <div class="item" style="left:480px;top:586px;width:198px;height:264px">
    <div class="wordmark" style="position:absolute;left:16px;top:42px;font-size:9px"><i class="dot" style="width:7px;height:7px"></i>Harrow Law LLC</div>
    <div class="address" style="position:absolute;left:64px;top:16px;padding-left:6px;font-size:7px;height:24px">Your address, City<br>State, Zip 1234</div>
  </div>

  <!-- Mailing label / compliments front -->
  <div class="item pattern" style="left:810px;top:570px;width:275px;height:130px" role="img" aria-label="Repeating orange chevron pattern"></div>

  <!-- Compliments card -->
  <div class="item" style="left:808px;top:733px;width:275px;height:130px">
    <div class="wordmark" style="position:absolute;left:10px;top:54px;font-size:13px"><i class="dot" style="width:10px;height:10px"></i>Harrow Law LLC</div>
    <div style="position:absolute;left:203px;top:31px;font-size:5.2px;line-height:1.35">Your address, City<br>State, Zip 1234</div>
    <ul class="contact" style="position:absolute;left:203px;top:47px;font-size:5.2px">
      <li><i class="ico"></i>123 456 789</li><li><i class="ico"></i>info@harrowlawllc.com</li><li><i class="ico"></i>www.harrowlawllc.com</li>
    </ul>
    <div class="compliments">with <span>compliments</span></div>
  </div>
</main>
</body>
</html>
```